New website for out outstanding veterinary training center

We already have a beautiful logo with nice colors and we are now looking for a breathtaking modern website to present our training center and future corses held there. A section to book open courses should also be available.

We are planing the realize the website with Wordpress.
The following pages should be available:
- Startpage / Overview
- Page to present the different rooms and seating option
- Page where the rooms can be booked
- Page where recommended accommodation are presented
- Page to present and book corses
- contact page
- Impressum

Target Market(s)

European Union

Industry/Entity Type

Education, Veterinary medicine

Number of Pages Required

5+ page

Font styles to use
Sans Serif

Colors
00AB8E
00BBA5
67D7C9
C6EFE9
E9F9F6

Requirements
Must have
• The website must be clear and easy to read. The colors form the logos should be used for the design.
Should not have
• To playful design. The page is not for a veterinary practice. we are a training center for veterinarians!

```html
<!DOCTYPE html>
<html lang="en">
<head>
<meta charset="utf-8">
<title>Veterra Training Center – Accommodation</title>
<link href="https://fonts.googleapis.com/css2?family=Lato:wght@400;700;900&display=swap" rel="stylesheet">
<style>
  :root {
    --teal: #00AB8E;
    --teal-bright: #1BB89C;
    --teal-head: #00BBA5;
    --teal-dark: #17736d;
    --mint-pale: #E6F6F4;
    --ink: #3e3338;
    --text: #3f3a3d;
    --footer: #45363F;
    --white: #ffffff;
  }
  * { box-sizing: border-box; margin: 0; padding: 0; }
  html, body { width: 680px; height: 1200px; overflow: hidden; }
  body { position: relative; font-family: "Lato", sans-serif; color: var(--text); background: var(--white); }

  .top-bar { position: absolute; left: 0; top: 0; width: 680px; height: 33px; background: var(--mint-pale); }
  .social { position: absolute; display: flex; gap: 12px; }
  .social span { width: 10px; height: 10px; border-radius: 50%; background: var(--ink); display: block; }
  .top-bar .social { left: 438px; top: 11px; }
  .btn-top { position: absolute; left: 556px; top: 5px; width: 82px; height: 22px; border-radius: 11px; background: var(--teal-bright); color: var(--white); font-size: 8.5px; font-weight: 700; display: flex; align-items: center; justify-content: center; }

  .brand { position: absolute; left: 44px; top: 12px; width: 84px; text-align: center; }
  .brand-mark { width: 50px; height: 50px; border-radius: 50%; background: var(--teal-dark); margin: 0 auto 4px; border: 4px solid var(--white); }
  .brand-name { font-size: 15px; font-weight: 900; color: var(--ink); line-height: 1; }

  .main-nav { position: absolute; top: 58px; right: 41px; display: flex; gap: 20px; font-size: 9.5px; font-weight: 700; color: var(--ink); }
  .main-nav .active { color: var(--teal-bright); }

  .hero { position: absolute; left: 0; top: 96px; width: 680px; height: 160px; background: linear-gradient(90deg, #3b4446 0%, #3f5756 40%, #1f7a72 75%, #157067 100%); }
  .hero-title { position: absolute; right: 41px; top: 40px; font-size: 32px; font-weight: 700; color: var(--white); }
  .hero-curve { position: absolute; left: 0; bottom: 0; }

  .section-title { position: absolute; top: 290px; width: 680px; text-align: center; font-size: 24px; font-weight: 900; color: var(--ink); }
  .section-rule { position: absolute; left: 319px; top: 328px; width: 42px; height: 2px; background: var(--teal-dark); }

  .stay { position: absolute; left: 42px; width: 596px; height: 176px; }
  .stay-photo { position: absolute; left: 0; top: 0; width: 291px; height: 176px; border-radius: 10px; }
  .stay-body { position: absolute; left: 306px; top: 8px; width: 290px; }
  .stay-body h3 { font-size: 13.6px; font-weight: 900; color: var(--ink); margin-bottom: 3px; }
  .stay-body p { font-size: 9px; line-height: 17.8px; }
  .btn-more { position: absolute; left: 307px; top: 132px; width: 101px; height: 31px; border-radius: 16px; background: var(--teal-bright); color: var(--white); font-size: 10px; font-weight: 700; display: flex; align-items: center; justify-content: center; }

  .site-footer { position: absolute; left: 0; top: 974px; width: 680px; height: 226px; background: var(--footer); color: var(--white); }
  .footer-brand { position: absolute; left: 42px; top: 55px; width: 126px; text-align: center; }
  .footer-brand .brand-mark { width: 78px; height: 78px; background: none; border: 3px solid var(--white); }
  .footer-brand .brand-name { color: var(--white); font-size: 20px; }
  .footer-col { position: absolute; top: 36px; }
  .footer-col h4 { font-size: 14px; font-weight: 900; color: var(--teal-head); margin-bottom: 4px; }
  .footer-col li { list-style: none; font-size: 9px; line-height: 18.8px; }
  .footer-col p { font-size: 9px; line-height: 16px; margin-bottom: 3px; }
  .footer-col .social { position: static; margin-top: 14px; gap: 12px; }
  .footer-col .social span { background: var(--teal-head); }
  .email-field { width: 137px; height: 26px; border-radius: 13px; background: var(--white); color: var(--ink); font-size: 9px; padding-left: 10px; display: flex; align-items: center; margin-top: 8px; }
  .btn-subscribe { width: 137px; height: 26px; border-radius: 13px; background: var(--teal-bright); font-size: 12px; font-weight: 900; display: flex; align-items: center; justify-content: center; margin-top: 8px; }
</style>
</head>
<body>
  <header>
    <div class="top-bar">
      <div class="social"><span></span><span></span><span></span><span></span><span></span></div>
      <a class="btn-top">Book Course</a>
    </div>
    <div class="brand"><div class="brand-mark"></div><div class="brand-name">Veterra</div></div>
    <nav class="main-nav">
      <span>Home</span><span>About Us</span><span>Rooms</span><span>Book Course</span><span class="active">Accommodation</span><span>Impressum</span><span>Contact Us</span>
    </nav>
  </header>

  <section class="hero" role="img" aria-label="Veterinary trainer greeting a cat in a clinic, tinted teal">
    <h1 class="hero-title">Accommodation</h1>
    <svg class="hero-curve" width="680" height="40" viewBox="0 0 680 40">
      <path d="M0 22 Q180 -6 340 40 Q500 -6 680 22 L680 40 L0 40 Z" fill="#ffffff"/>
    </svg>
  </section>

  <h2 class="section-title">Accommodation</h2>
  <div class="section-rule"></div>

  <article class="stay" style="top:362px">
    <div class="stay-photo" role="img" aria-label="Two young women meeting in a bright shared guest room" style="background:linear-gradient(120deg,#b08a72,#d8cbc0 55%,#ece8e6)"></div>
    <div class="stay-body"><h3>Heading Title</h3><p>Sed ut perspiciatis unde omnis iste natus error sit voluptatem accusantium doloremque laudantium, totam rem aperiam, eaque ipsa quae ab illo inventore veritatis et quasi architecto beatae vitae dicta sunt explicab emo enim ipsam voluptatem quia voluptas sit aspernatur aut odit aut fugit, sed quia.</p></div>
    <a class="btn-more">More Info</a>
  </article>

  <article class="stay" style="top:561px">
    <div class="stay-photo" role="img" aria-label="Student working on a laptop at a desk in a single room" style="background:linear-gradient(120deg,#3d4a7a,#d9d0c2 50%,#8c6a4a)"></div>
    <div class="stay-body"><h3>Heading Title</h3><p>Sed ut perspiciatis unde omnis iste natus error sit voluptatem accusantium doloremque laudantium, totam rem aperiam, eaque ipsa quae ab illo inventore veritatis et quasi architecto beatae vitae dicta sunt explicab emo enim ipsam voluptatem quia voluptas sit aspernatur aut odit aut fugit, sed quia.</p></div>
    <a class="btn-more">More Info</a>
  </article>

  <article class="stay" style="top:760px">
    <div class="stay-photo" role="img" aria-label="Guests relaxing in a dormitory with white bunk beds" style="background:linear-gradient(120deg,#e8e4e0,#3f5a9a 50%,#d9d2c6)"></div>
    <div class="stay-body"><h3>Heading Title</h3><p>Sed ut perspiciatis unde omnis iste natus error sit voluptatem accusantium doloremque laudantium, totam rem aperiam, eaque ipsa quae ab illo inventore veritatis et quasi architecto beatae vitae dicta sunt explicab emo enim ipsam voluptatem quia voluptas sit aspernatur aut odit aut fugit, sed quia.</p></div>
    <a class="btn-more">More Info</a>
  </article>

  <footer class="site-footer">
    <div class="footer-brand"><div class="brand-mark"></div><div class="brand-name">Veterra</div></div>
    <div class="footer-col" style="left:207px">
      <h4>Site Map</h4>
      <ul><li>Home</li><li>About Us</li><li>Rooms</li><li>Book Course</li><li>Accommodation</li><li>Impressum</li><li>Contact Us</li></ul>
    </div>
    <div class="footer-col" style="left:343px">
      <h4>Contact Us</h4>
      <p>Neque porro quisquam<br>est,qui dolorem</p>
      <p>1-800-555-0142</p>
      <p>info@veterra-academy.eu</p>
      <div class="social"><span></span><span></span><span></span><span></span><span></span></div>
    </div>
    <div class="footer-col" style="left:502px">
      <h4>Email Subscribe</h4>
      <p>Neque porro quisquam est,<br>qui dolorem</p>
      <div class="email-field">Email Address</div>
      <div class="btn-subscribe">Subscribe</div>
    </div>
  </footer>
</body>
</html>
```